KAJU Freightways #ALLKAJU Business Cards & Letterhead

I am looking to business cards designed for our organization. We are currently undergoing a small re-branding that is taking place. Our organization is called KAJU Freightways and we are headquartered in Phoenix, AZ. We primarily provide transportation and logistics services to the Marlow Parcel Bureau who is our largest customer. I would like to see a design that incorporates name, title, contact info, website, and address (this will be different depending on the employee). I would also like to see some color on the business card using our logo colors or a variation. I would like our logo on the back of the business card with the website displayed. The final design should communicate that we are a next generation transportation operate that focuses on being driver-first, customer-centric, innovative, and sustainable.We would also like our #ALLKAJU catch phrase incorporated as well.

Target Market(s)

Transportation & Logistics

Industry/Entity Type

Trucking Company

Contact Information for Business Card

-First and Last Name
-Position Title
-Contact Phone
-Contact Email
-Physical Address

Font styles to use
Serif

Colors

Designer to choose colors to be used in the design.

Requirements
Must have
• -KAJU logo prominently displayed
• -#ALLKAJU catch phrase used
• -Some amount of color, design gradient, etc.
• -Logo on the back with website listed (https://www.kajufreightco.example)

```html
<!DOCTYPE html>
<html lang="en">
<head>
<meta charset="utf-8">
<title>KAJU Freightways Business Card</title>
<link href="https://fonts.googleapis.com/css2?family=Lora:wght@400;700&display=swap" rel="stylesheet">
<style>
  :root {
    --backdrop: #2a2a2a;
    --paper: #ffffff;
    --teal: #033d47;
    --green: #7dc242;
    --ink: #3a3a3a;
    --rule: #b5b5b5;
  }
  html, body { margin: 0; padding: 0; overflow: hidden; }
  body { width: 1200px; height: 1200px; background: var(--backdrop); position: relative; font-family: "Lora", serif; }
  .card { position: absolute; top: 310px; height: 594px; box-shadow: 0 4px 10px rgba(0,0,0,.45); overflow: hidden; }
  .card-front { left: 234px; width: 364px; background: var(--paper); }
  .card-back { left: 628px; width: 368px; background: var(--teal); }

  .brand { position: absolute; left: 0; right: 0; display: flex; align-items: center; justify-content: center; gap: 12px; }
  .brand-dot { border-radius: 50%; background: var(--green); flex: none; }
  .brand-name { font-family: "Lora", serif; font-weight: 700; line-height: 1; letter-spacing: 2px; }
  .card-front .brand { top: 133px; }
  .card-front .brand-dot { width: 22px; height: 22px; }
  .card-front .brand-name { font-size: 60px; color: var(--teal); }
  .card-back .brand { top: 256px; }
  .card-back .brand-dot { width: 28px; height: 28px; }
  .card-back .brand-name { font-size: 74px; color: var(--paper); }

  .centered { position: absolute; left: 0; right: 0; text-align: center; margin: 0; line-height: 22px; white-space: nowrap; }
  .person-name { top: 311px; font-size: 20px; font-weight: 700; color: var(--green); letter-spacing: .3px; }
  .person-title { top: 333px; font-size: 16px; color: var(--ink); }
  .icon-row { position: absolute; top: 362px; left: 87px; width: 190px; height: 26px; }
  .contact-line { font-size: 16px; color: var(--ink); }
  .phone { top: 397px; }
  .email { top: 419px; }
  .web { top: 441px; color: var(--teal); }
  .web .accent { color: var(--green); }
  .divider { position: absolute; top: 471px; left: 97px; width: 182px; height: 1px; background: var(--rule); }
  .company { top: 481px; font-size: 16px; color: var(--teal); }
  .address { font-size: 16px; color: var(--ink); }
  .address-1 { top: 503px; }
  .address-2 { top: 525px; }
  .tagline { top: 360px; font-size: 18px; font-weight: 700; color: var(--green); letter-spacing: 2px; }
  .back-web { top: 533px; font-size: 15px; color: var(--green); }
</style>
</head>
<body>
  <section class="card card-front">
    <div class="brand"><span class="brand-name">KAJU</span><span class="brand-dot"></span></div>
    <p class="centered person-name">DANIEL REEVE</p>
    <p class="centered person-title">Managing Director</p>
    <svg class="icon-row" viewBox="0 0 190 26" aria-hidden="true">
      <line x1="0" y1="13" x2="55" y2="13" stroke="#b5b5b5" stroke-width="1.5"/>
      <line x1="135" y1="13" x2="190" y2="13" stroke="#b5b5b5" stroke-width="1.5"/>
      <circle cx="67" cy="13" r="12" fill="#7dc242"/>
      <circle cx="94" cy="13" r="12" fill="#7dc242"/>
      <circle cx="121" cy="13" r="12" fill="#7dc242"/>
      <path d="M61 16h12v3H61z M62 13c0-4 10-4 10 0" fill="none" stroke="#fff" stroke-width="1.6"/>
      <rect x="87" y="8" width="14" height="10" fill="none" stroke="#fff" stroke-width="1.5"/>
      <path d="M87 8l7 6 7-6" fill="none" stroke="#fff" stroke-width="1.5"/>
      <circle cx="121" cy="13" r="6.5" fill="none" stroke="#fff" stroke-width="1.5"/>
      <path d="M114.5 13h13 M121 6.5c-3 3-3 10 0 13 M121 6.5c3 3 3 10 0 13" fill="none" stroke="#fff" stroke-width="1.1"/>
    </svg>
    <p class="centered contact-line phone">044-555 010 234</p>
    <p class="centered contact-line email">info@kajufreight.example</p>
    <p class="centered contact-line web">www.<span class="accent">kajufreightco</span>.example</p>
    <div class="divider"></div>
    <p class="centered company">KAJU Freightways</p>
    <p class="centered address address-1">421, Address line here,</p>
    <p class="centered address address-2">45452, Country Name</p>
  </section>

  <section class="card card-back">
    <div class="brand"><span class="brand-name">KAJU</span><span class="brand-dot"></span></div>
    <p class="centered tagline">#ALLKAJU</p>
    <p class="centered back-web">www.kajufreightco.example</p>
  </section>
</body>
</html>
```